business card deign

Logo needs the following on it.
1. attached logo
2. Tagline - "From chilled coolers to all-night tunes...we bring it!"
3. Name- Dalton Pikes, Founder and CPO
4. Address - 412 E. Carver Avenue, Ste 2207, Tampa, FL. 33917
5. Phone - 555.318.4726

```html
<!DOCTYPE html>
<html lang="en">
<head>
<meta charset="utf-8">
<title>Kooley Business Card</title>
<link rel="stylesheet" href="https://fonts.googleapis.com/css2?family=Roboto+Condensed:wght@400;700&family=Roboto:wght@400&display=swap">
<style>
  :root {
    --backdrop: #6f6f70;
    --ink: #111111;
    --card-dark: #141414;
    --paper: #ffffff;
  }
  * { box-sizing: border-box; margin: 0; padding: 0; }
  html, body {
    width: 900px;
    height: 1200px;
    overflow: hidden;
    background: var(--backdrop);
  }
  .canvas {
    position: relative;
    width: 900px;
    height: 1200px;
  }
  .card {
    position: absolute;
    width: 631px;
    height: 358px;
  }
  .card-front {
    left: 134px;
    top: 214px;
    background: var(--card-dark);
  }
  .card-back {
    left: 135px;
    top: 628px;
    background: var(--paper);
    color: var(--ink);
  }
  .brand-name {
    font-family: "Roboto", sans-serif;
    font-weight: 400;
    letter-spacing: 0;
  }
  .card-front .brand-name {
    position: absolute;
    left: 0;
    right: 0;
    top: 152px;
    text-align: center;
    font-size: 48px;
    line-height: 1;
    color: var(--paper);
  }
  .card-back .brand-name {
    position: absolute;
    left: 120px;
    top: 164px;
    width: 200px;
    text-align: center;
    font-size: 32px;
    line-height: 1;
    color: var(--ink);
  }
  .divider {
    position: absolute;
    left: 341px;
    top: 98px;
    width: 2px;
    height: 164px;
    background: var(--ink);
  }
  .contact {
    position: absolute;
    left: 368px;
    top: 108px;
  }
  .contact-name {
    font-family: "Roboto Condensed", sans-serif;
    font-weight: 700;
    font-size: 28px;
    line-height: 1;
    text-transform: uppercase;
  }
  .contact-title,
  .contact-address {
    font-family: "Roboto", sans-serif;
    font-size: 15px;
    line-height: 1;
  }
  .contact-title { margin-top: 12px; }
  .contact-phone {
    display: flex;
    align-items: center;
    gap: 6px;
    margin-top: 20px;
    font-family: "Roboto", sans-serif;
    font-size: 17px;
    letter-spacing: 0.04em;
    line-height: 1;
  }
  .contact-phone svg { width: 12px; height: 12px; }
  .contact-address { margin-top: 16px; line-height: 25px; }
  .tagline {
    position: absolute;
    left: 0;
    right: 0;
    top: 302px;
    text-align: center;
    font-family: "Roboto Condensed", sans-serif;
    font-weight: 700;
    font-size: 15px;
    letter-spacing: 0.04em;
  }
</style>
</head>
<body>
<main class="canvas">
  <section class="card card-front">
    <div class="brand-name">Kooley</div>
  </section>

  <section class="card card-back">
    <div class="brand-name">Kooley</div>
    <div class="divider"></div>
    <div class="contact">
      <h1 class="contact-name">Dalton Pikes</h1>
      <p class="contact-title">Founder and CPO</p>
      <p class="contact-phone">
        <svg viewBox="0 0 24 24" aria-hidden="true"><path fill="#111" d="M6.6 10.8a15.1 15.1 0 0 0 6.6 6.6l2.2-2.2a1 1 0 0 1 1-.25 11.4 11.4 0 0 0 3.6.57 1 1 0 0 1 1 1V20a1 1 0 0 1-1 1A17 17 0 0 1 3 4a1 1 0 0 1 1-1h3.5a1 1 0 0 1 1 1c0 1.25.2 2.45.57 3.57a1 1 0 0 1-.25 1z"/></svg>
        555.318.4726
      </p>
      <p class="contact-address">412 E. Carver Avenue, Ste 2207<br>Tampa, FL. 33917</p>
    </div>
    <p class="tagline">From chilled coolers to all-night tunes...we bring it!</p>
  </section>
</main>
</body>
</html>
```